Permanent Makeup (cosmetics salon) Brochure

We need a 2-4 sites brochure for our Permanent Makeup (cosmetics salon). Our company is based in Austria / Vienna. -> Our homepage is www.ek-morgenstaller.at
This brochure should show which treatments we provide ot our customers.

I've uploaded our old brochure, the content (text) would be nearly the same (look form "Must Haves", pics have to be new (look uploaded pics)
The old brochure is to dark. -> look for our homepage maybe you can make it like this

Target Market(s)

woman, age 25-70 years who wants to have permanent makeup on eyebrows, lips or eyeliner

Industry/Entity Type

Beauty Salon

Requirements
Must have
• pics which are uploaded.

*This text (somithing about our business)
"Für Frau Morgenstaller ist Permanent Makeup ein Kunsthandwerk. Das Team von EK-Morgenstaller ist spezialisiert auf natürliches Permanent Makeup damit der individuelle Typ jeder Kundin am schönsten zum Ausdruck kommt."

*We do this treatments: (english)
+ Augenbrauen Microblading (eyebrows)
+ Augenbrauen Permanent Makeup (eyebrows2)
+ Lidstrich Permanent Makeup (eyeliner)
+ Lip Blushing (lips)
+ Lippen Permanent Makeup (lips2)

* Our addresses (2 locations)
Wien
Lindengasse 7b/12, 1010 Wien
Tel: 01/5827710

Villach
Birkenrainweg 4, 9524 St. Ulrich
Tel: 0676/3159082

Mail: info@ek-morgenstaller.at
www.ek-morgenstaller.at

```html
<!DOCTYPE html>
<html lang="de">
<head>
<meta charset="utf-8">
<title>Elena Morgenstaller Kosmetikstudio – Broschüre</title>
<link rel="stylesheet" href="https://fonts.googleapis.com/css2?family=Josefin+Sans:wght@300;400&family=Lato:wght@400&family=Oswald:wght@200;300&display=swap">
<style>
:root{
  --slate:#3a4257;
  --slate-light:#5b6679;
  --gold:#e2b95c;
  --gold-deep:#d6a944;
  --paper:#f1f1f2;
  --ink:#3b3f4a;
  --white:#ffffff;
  --backdrop:#d9d9db;
}
*{margin:0;padding:0;box-sizing:border-box}
html,body{width:1200px;height:1164px;overflow:hidden;background:var(--backdrop)}
body{position:relative;font-family:"Josefin Sans",sans-serif;color:var(--ink)}
.spread{position:absolute;left:60px;width:1080px;height:540px;overflow:hidden;box-shadow:0 6px 18px rgba(0,0,0,.25)}
.spread-cover{top:28px}
.spread-inner{top:596px}
.page{position:absolute;top:0;width:540px;height:540px;overflow:hidden}
.page-left{left:0}
.page-right{left:540px}
.spine{position:absolute;left:537px;top:0;width:6px;height:540px;background:linear-gradient(90deg,rgba(0,0,0,0),rgba(0,0,0,.12),rgba(0,0,0,0));z-index:5}
.photo{position:absolute}
.overlay{position:absolute;left:0;top:0;z-index:2}
.abs{position:absolute;z-index:3}
.center{text-align:center}

/* brand */
.brand{display:flex;align-items:center;justify-content:center;gap:10px;white-space:nowrap}
.brand-name{font-family:"Josefin Sans",sans-serif;font-weight:400}
.brand-dot{border:2px solid var(--gold);border-radius:50%}
.brand-sub{font-family:"Lato",sans-serif;font-size:8px;letter-spacing:4px;color:var(--white)}

/* cover spread */
.dark-panel{position:absolute;left:0;top:210px;width:540px;height:330px;background:linear-gradient(180deg,var(--slate-light),var(--slate) 60%)}
.headline-gold{font-family:"Josefin Sans",sans-serif;font-weight:300;color:var(--gold);font-size:17px;letter-spacing:.2px}
.contact{left:31px;font-family:"Lato",sans-serif;color:var(--white);font-size:8.6px;line-height:13.6px}
.contact h3{font-weight:400;color:var(--gold);font-size:10px;margin-bottom:3px}
.contact p{display:flex;align-items:center;gap:5px}
.contact svg{width:7px;height:7px;flex:none}
.socials{display:flex;gap:12px}
.socials span{width:18px;height:18px;border:1px solid var(--white);border-radius:50%;opacity:.9}
.url-pill{height:23px;border-radius:12px;background:var(--slate);color:var(--white);font-family:"Josefin Sans",sans-serif;font-weight:300;font-size:12.5px;display:flex;align-items:center;justify-content:center;box-shadow:0 2px 4px rgba(0,0,0,.25)}
.light-page{background:linear-gradient(180deg,#f7f8f9,#e9ecee)}
.tagline{font-family:"Oswald",sans-serif;font-weight:300;font-size:6.5px;letter-spacing:.3px;color:#222}
.claim-big{font-family:"Oswald",sans-serif;font-weight:200;font-size:44px;color:var(--slate);letter-spacing:-1px}
.claim-mid{font-family:"Josefin Sans",sans-serif;font-weight:300;font-size:18px;color:var(--slate)}
.claim-von{display:flex;align-items:center;gap:10px}
.claim-von i{display:block;width:42px;height:1px;background:var(--gold)}
.claim-end{font-family:"Josefin Sans",sans-serif;font-weight:300;font-size:34px;color:var(--slate);letter-spacing:1px}

/* inner spread */
.paper{position:absolute;left:0;top:253px;width:540px;height:287px;background:var(--paper);border-top:2px solid var(--gold)}
.dark-top{position:absolute;left:0;top:0;width:540px;height:253px;background:linear-gradient(180deg,var(--slate),var(--slate-light))}
.section-title{font-family:"Josefin Sans",sans-serif;font-weight:300;color:var(--gold);font-size:16.5px}
.about{font-family:"Josefin Sans",sans-serif;font-weight:300;font-size:13.4px;line-height:25.5px;color:var(--ink)}
.treatments{list-style:none;font-family:"Josefin Sans",sans-serif;font-weight:300;font-size:14.2px;line-height:25.5px;color:var(--ink)}
.treatments li{display:flex;align-items:center;gap:12px}
.treatments svg{width:13px;height:13px;flex:none}
.footer-band{position:absolute;left:0;top:491px;width:540px;height:30px;background:var(--slate-light);color:var(--white);font-family:"Josefin Sans",sans-serif;font-weight:300;font-size:12.5px;display:flex;align-items:center;justify-content:center;z-index:3}
.footer-band.right{background:linear-gradient(90deg,var(--slate-light),var(--slate))}
.detail{position:absolute;border-radius:50%;border:4px solid var(--gold);z-index:3}
</style>
</head>
<body>

<!-- Cover spread -->
<section class="spread spread-cover">
  <div class="page page-left">
    <div class="photo" role="img" aria-label="Team photo: five beauticians in dark uniforms in a bright salon" style="left:0;top:0;width:540px;height:208px;background:linear-gradient(90deg,#f3ede4,#d9c9b3 40%,#e8dccb 70%,#f1e9dd)"></div>
    <div class="dark-panel"></div>
    <div style="position:absolute;left:0;top:208px;width:540px;height:2px;background:#9aa1ad"></div>
  </div>
  <div class="page page-right light-page">
    <div class="photo" role="img" aria-label="Beauty portrait of a young woman with her hand raised to her cheek" style="left:250px;top:0;width:290px;height:540px;background:linear-gradient(90deg,rgba(241,236,232,0),#e9c9b0 35%,#dcae8f 70%,#c89778)"></div>
  </div>

  <svg class="overlay" width="1080" height="540" viewBox="0 0 1080 540" aria-hidden="true">
    <circle cx="557" cy="736" r="377" fill="#ffffff" opacity=".92"/>
    <circle cx="553" cy="738" r="371" fill="#e2b95c"/>
  </svg>

  <!-- left page text -->
  <div class="abs brand" style="left:0;top:262px;width:540px">
    <span class="brand-name" style="color:var(--white);font-size:22px">Elena Morgenstaller</span>
    <span class="brand-dot" style="width:22px;height:22px"></span>
  </div>
  <div class="abs brand-sub center" style="left:0;top:308px;width:540px">KOSMETIKSTUDIO</div>
  <div class="abs headline-gold center" style="left:0;top:343px;width:540px">IHR KOSMETIKSTUDIO UND BEAUTY SALON</div>

  <div class="abs contact" style="top:394px">
    <h3>WIEN</h3>
    <p><svg viewBox="0 0 10 10"><path d="M5 0a3.4 3.4 0 0 0-3.4 3.4C1.6 6 5 10 5 10s3.4-4 3.4-6.6A3.4 3.4 0 0 0 5 0zm0 4.8a1.4 1.4 0 1 1 0-2.8 1.4 1.4 0 0 1 0 2.8z" fill="#fff"/></svg>Lindengasse 7b/12, 1010 Wien</p>
    <p><svg viewBox="0 0 10 10"><path d="M2.2 0.5l1.6 2.2-1 1.2c.6 1.3 1.7 2.4 3 3l1.2-1 2.2 1.6-.9 1.8C4.700 9 .9 5.3 .5 1.4z" fill="#fff"/></svg>01/5827710</p>
    <p><svg viewBox="0 0 10 10"><path d="M1 2h8v6H1zM1 2l4 3 4-3" fill="none" stroke="#fff"/></svg>info@ek-morgenstaller.at</p>
  </div>
  <div class="abs contact" style="top:464px">
    <h3>VILLACH</h3>
    <p><svg viewBox="0 0 10 10"><path d="M5 0a3.4 3.4 0 0 0-3.4 3.4C1.6 6 5 10 5 10s3.4-4 3.4-6.6A3.4 3.4 0 0 0 5 0zm0 4.8a1.4 1.4 0 1 1 0-2.8 1.4 1.4 0 0 1 0 2.8z" fill="#fff"/></svg>Birkenrainweg 4, 9524 St. Ulrich</p>
    <p><svg viewBox="0 0 10 10"><path d="M2.2 0.5l1.6 2.2-1 1.2c.6 1.3 1.7 2.4 3 3l1.2-1 2.2 1.6-.9 1.8C4.7 9 .9 5.3 .5 1.4z" fill="#fff"/></svg>0676/3159082</p>
    <p><svg viewBox="0 0 10 10"><path d="M1 2h8v6H1zM1 2l4 3 4-3" fill="none" stroke="#fff"/></svg>info@ek-morgenstaller.at</p>
  </div>

  <div class="abs socials" style="left:409px;top:465px"><span></span><span></span><span></span><span></span></div>
  <div class="abs url-pill" style="left:310px;top:495px;width:218px">www.ek-morgenstaller.at</div>

  <!-- right page text -->
  <div class="abs brand" style="left:540px;top:100px;width:290px">
    <span class="brand-name" style="color:#222;font-size:17px">Elena Morgenstaller</span>
    <span class="brand-dot" style="width:18px;height:18px"></span>
  </div>
  <div class="abs tagline center" style="left:540px;top:134px;width:290px">WAS IHNEN WERTVOLL IST, GEHÖRT IN GUTE HÄNDE</div>
  <div class="abs claim-big" style="left:591px;top:188px">SCHÖNHEIT</div>
  <div class="abs claim-mid" style="left:591px;top:245px">kommt nicht nur</div>
  <div class="abs claim-mid claim-von" style="left:591px;top:276px"><i></i>von<i></i></div>
  <div class="abs claim-end" style="left:618px;top:298px">innen</div>

  <div class="abs socials" style="left:565px;top:465px"><span></span><span></span><span></span><span></span></div>
  <div class="abs url-pill" style="left:563px;top:495px;width:218px">www.ek-morgenstaller.at</div>

  <div class="spine"></div>
</section>

<!-- Inner spread -->
<section class="spread spread-inner">
  <div class="page page-left">
    <div class="photo" role="img" aria-label="Close-up of a woman's eye with a defined brow and soft makeup" style="left:0;top:0;width:540px;height:253px;background:linear-gradient(100deg,#e9c7ad,#d7a585 45%,#c98a68 75%,#e7d2b5)"></div>
    <div class="paper"></div>
    <svg class="overlay" width="540" height="540" viewBox="0 0 540 540" aria-hidden="true">
      <ellipse cx="0" cy="540" rx="276" ry="145" fill="#ffffff"/>
      <ellipse cx="0" cy="540" rx="268" ry="141" fill="#e2b95c"/>
    </svg>
    <div class="abs section-title center" style="left:0;top:302px;width:540px">IHR KOSMETIKSTUDIO UND BEAUTY SALON</div>
    <p class="abs about center" style="left:30px;top:337px;width:480px">Für Frau Morgenstaller ist Permanent Makeup ein Kunsthandwerk. Das Team von EK-Morgenstaller ist spezialisiert auf natürliches Permanent Makeup damit der individuelle Typ jeder Kundin am schönsten zum Ausdruck kommt.</p>
    <div class="footer-band">www.ek-morgenstaller.at</div>
  </div>

  <div class="page page-right">
    <div class="dark-top"></div>
    <div class="paper" style="z-index:1"></div>
    <div class="abs brand" style="left:0;top:55px;width:540px">
      <span class="brand-name" style="color:var(--white);font-size:22px">Elena Morgenstaller</span>
      <span class="brand-dot" style="width:22px;height:22px"></span>
    </div>
    <div class="abs brand-sub center" style="left:0;top:98px;width:540px">KOSMETIKSTUDIO</div>

    <div class="detail" role="img" aria-label="Close-up of an eye with permanent eyeliner" style="left:109px;top:152px;width:114px;height:114px;background:radial-gradient(circle,#9fb3ad,#e8cfc2 60%)"></div>
    <div class="detail" role="img" aria-label="Close-up of lips with lip blushing" style="left:334px;top:152px;width:114px;height:114px;background:radial-gradient(circle,#8a6650,#e8c4ac 60%)"></div>
    <div class="detail" role="img" aria-label="Close-up of full lips with permanent lip colour" style="left:201px;top:137px;width:144px;height:144px;z-index:4;background:radial-gradient(circle,#d07a74,#e5a79b 55%,#efc9bb)"></div>

    <div class="abs section-title center" style="left:0;top:302px;width:540px">WE DO THIS TREATMENTS:</div>
    <ul class="abs treatments" style="left:60px;top:334px">
      <li><svg viewBox="0 0 14 14"><circle cx="7" cy="7" r="6" fill="none" stroke="#e2b95c"/><path d="M6 4.5L8.5 7 6 9.5" fill="none" stroke="#e2b95c" stroke-width="1.3"/></svg>Augenbrauen Microblading (eyebrows)</li>
      <li><svg viewBox="0 0 14 14"><circle cx="7" cy="7" r="6" fill="none" stroke="#e2b95c"/><path d="M6 4.5L8.5 7 6 9.5" fill="none" stroke="#e2b95c" stroke-width="1.3"/></svg>Augenbrauen Permanent Makeup (eyebrows2)</li>
      <li><svg viewBox="0 0 14 14"><circle cx="7" cy="7" r="6" fill="none" stroke="#e2b95c"/><path d="M6 4.5L8.5 7 6 9.5" fill="none" stroke="#e2b95c" stroke-width="1.3"/></svg>Lidstrich Permanent Makeup (eyeliner)</li>
      <li><svg viewBox="0 0 14 14"><circle cx="7" cy="7" r="6" fill="none" stroke="#e2b95c"/><path d="M6 4.5L8.5 7 6 9.5" fill="none" stroke="#e2b95c" stroke-width="1.3"/></svg>Lip Blushing (lips)</li>
      <li><svg viewBox="0 0 14 14"><circle cx="7" cy="7" r="6" fill="none" stroke="#e2b95c"/><path d="M6 4.5L8.5 7 6 9.5" fill="none" stroke="#e2b95c" stroke-width="1.3"/></svg>Lippen Permanent Makeup (lips2)</li>
    </ul>
    <div class="footer-band right">www.ek-morgenstaller.at</div>
    <div style="position:absolute;left:0;top:521px;width:540px;height:19px;background:var(--paper);z-index:3"></div>
  </div>

  <div class="spine"></div>
</section>

</body>
</html>
```